Business card for Luxury Portable Restroom Trailer company

We are a Luxury Portable Restroom Trailer Company Called FALCRIDGE HIRES. Based in Orange County California. We provide portable restroom trailers for events, such as, Weddings, Concerts, Charity events, Sporting events, Tournaments, Corporate events, ect. We rent and Sell the Luxury restrooms. Our colors are white, grey, and Orange. As you will see in the logo we uploaded.
There are 2 people in the company so the names and titles will change for the 3 people but card will remain the same. Here is the information for each Person: Dwight Penner CFO 555 318-0476
next Person: Leon Marchetti VP 555 318-0476
Next Person: Owen Marchetti CEO 555 318-0476
Information to include on the card: Luxury Restroom Trailers Rental and Sales. Weddings, Concerts, Charity, Sporting and Corp. Events.

```html
<!DOCTYPE html>
<html lang="en">
<head>
<meta charset="utf-8">
<title>Falcridge Hires — Business Card</title>
<link rel="stylesheet" href="https://fonts.googleapis.com/css2?family=Montserrat:wght@400;600;700;800&display=swap">
<style>
  :root {
    --bg: #e4e4e2;
    --card-white: #f6f6f6;
    --grey-dark: #444548;
    --grey-logo: #4f5053;
    --orange: #e2601f;
    --text-light: #f2f2f2;
    --text-soft: #d9d9d9;
  }
  * { margin: 0; padding: 0; box-sizing: border-box; }
  html, body { width: 1200px; height: 1200px; overflow: hidden; }
  body {
    background: var(--bg);
    font-family: "Montserrat", Arial, sans-serif;
    position: relative;
  }
  .card {
    position: absolute;
    left: 230px;
    width: 740px;
    height: 422px;
    overflow: hidden;
    box-shadow: 0 10px 24px rgba(0,0,0,0.22);
  }
  .card--front { top: 150px; background: var(--card-white); }
  .card--back  { top: 628px; background: var(--grey-dark); }

  .wordmark {
    position: absolute;
    text-align: center;
    font-weight: 800;
    color: var(--grey-logo);
    line-height: 1;
  }
  .card--front .wordmark { left: 84px; width: 574px; top: 72px; }
  .card--front .wordmark__main { font-size: 76px; letter-spacing: 1px; display: block; }
  .card--front .wordmark__sub { font-size: 42px; letter-spacing: 6px; display: block; margin-top: 10px; }

  .services {
    position: absolute;
    top: 252px;
    left: 83px;
    width: 575px;
    display: grid;
    grid-template-columns: 261px 261px;
    column-gap: 53px;
    row-gap: 13px;
  }
  .service {
    background: var(--orange);
    color: #fff;
    height: 25px;
    font-size: 17px;
    line-height: 25px;
    text-align: center;
    white-space: nowrap;
  }

  .back-art { position: absolute; inset: 0; }
  .card--back .wordmark { left: 372px; width: 323px; top: 44px; }
  .card--back .wordmark__main { font-size: 42px; display: block; }
  .card--back .wordmark__sub { font-size: 24px; letter-spacing: 4px; display: block; margin-top: 6px; }

  .person { position: absolute; left: 44px; top: 170px; }
  .person__name { font-size: 31px; font-weight: 700; color: var(--text-light); }
  .person__title { font-size: 19px; color: var(--text-soft); margin-top: 6px; }

  .contacts { position: absolute; left: 44px; top: 302px; list-style: none; }
  .contacts li {
    display: flex; align-items: center;
    height: 28px;
    font-size: 19px;
    color: var(--text-light);
  }
  .contacts svg { width: 16px; height: 16px; margin-right: 10px; fill: var(--text-light); }
  .contacts .accent { color: var(--orange); }

  .address {
    position: absolute;
    right: 45px; top: 330px;
    text-align: right;
    font-size: 19px;
    line-height: 28px;
    color: var(--text-light);
  }
</style>
</head>
<body>

<section class="card card--front" aria-label="Card front">
  <div class="wordmark">
    <span class="wordmark__main">FALCRIDGE</span>
    <span class="wordmark__sub">HIRES</span>
  </div>
  <div class="services">
    <div class="service">Luxury Restroom</div>
    <div class="service">Concerts</div>
    <div class="service">Trailers Rental and Sales</div>
    <div class="service">Charity</div>
    <div class="service">Weddings</div>
    <div class="service">Sporting and Corp. Events</div>
  </div>
</section>

<section class="card card--back" aria-label="Card back">
  <svg class="back-art" viewBox="0 0 740 422" width="740" height="422" aria-hidden="true">
    <path d="M85,0 L740,0 L740,216 C680,245 620,266 555,266 C380,266 230,160 85,0 Z" fill="#f2f2f2"/>
    <path d="M97,0 L145,0 C250,130 370,225 500,258 C350,235 210,140 97,0 Z" fill="#e2601f"/>
  </svg>

  <div class="wordmark">
    <span class="wordmark__main">FALCRIDGE</span>
    <span class="wordmark__sub">HIRES</span>
  </div>

  <div class="person">
    <p class="person__name">Dwight Penner</p>
    <p class="person__title">CFO</p>
  </div>

  <ul class="contacts">
    <li>
      <svg viewBox="0 0 24 24" aria-hidden="true"><path d="M6.6 10.8a15 15 0 0 0 6.6 6.6l2.2-2.2c.3-.3.7-.4 1-.2 1.1.4 2.3.6 3.6.6.6 0 1 .4 1 1V20c0 .6-.4 1-1 1A17 17 0 0 1 3 4c0-.6.4-1 1-1h3.5c.6 0 1 .4 1 1 0 1.3.2 2.5.6 3.6.1.3 0 .7-.2 1z"/></svg>
      555 318-0476
    </li>
    <li>
      <svg viewBox="0 0 24 24" aria-hidden="true"><path d="M2 5h20v14H2z M2 5l10 8 10-8" fill="none" stroke="#f2f2f2" stroke-width="0"/><path d="M2 5h20L12 12z M2 7v12h20V7l-10 7z"/></svg>
      info@falcridgehires.com
    </li>
    <li>
      <svg viewBox="0 0 24 24" aria-hidden="true"><path d="M12 2a10 10 0 1 0 0 20 10 10 0 0 0 0-20zm0 2c.9 0 2.2 2 2.7 5H9.3C9.8 6 11.1 4 12 4zM4.3 11h3c0 .7 0 1.3.1 2h-3a8 8 0 0 1-.1-2zm.5 4h2.8c.3 1.3.7 2.5 1.2 3.4A8 8 0 0 1 4.8 15zm2.8-6H4.8A8 8 0 0 1 8.8 5.6 12 12 0 0 0 7.6 9zM12 20c-.9 0-2.2-2-2.7-5h5.4c-.5 3-1.8 5-2.7 5zm-2.9-7a16 16 0 0 1 0-2h5.8a16 16 0 0 1 0 2zm6.1 5.4c.5-1 .9-2.1 1.2-3.4h2.8a8 8 0 0 1-4 3.4zM16.6 13c.1-.7.1-1.3.1-2h3a8 8 0 0 1 0 2zm-.2-4a12 12 0 0 0-1.2-3.4A8 8 0 0 1 19.2 9z"/></svg>
      www.<span class="accent">falcridgehires</span>.com
    </li>
  </ul>

  <address class="address" style="font-style:normal">
    4170 Alder Lane<br>
    Brook Hollow Maine 11408
  </address>
</section>

</body>
</html>
```